BRISKEL Need a luxury modern business card designed.

Need a luxury modern business card designed. refer to the uploaded files for the company name and logo in the zip file under source files. i will making my descion on monday. so please send in before then so if we need to edit we will have the time. we have a trade show coming up and im on a deadline for printer.

Target Market(s)

high end clients

Contact Information for Business Card

Company nAme and logo. Tobias Fennick Co-Founder / Project Manager Office # 555-318-7094 Cell # 555-642-1586 BRISKEL.CA Tobias@briskel-example.ca

Font styles to use
Other font styles liked:
• Modern

Requirements
Must have
• Company name and logo, contact info, using the black, gold and white color scheme.

```html
<!DOCTYPE html>
<html lang="en">
<head>
<meta charset="utf-8">
<title>BRISKEL Business Card</title>
<link rel="stylesheet" href="https://fonts.googleapis.com/css2?family=Jost:wght@400;500&family=Montserrat:wght@300;500;600;700&display=swap">
<style>
  :root {
    --stage: #cbcbcb;
    --charcoal: #333333;
    --ink: #2f2f2f;
    --white: #ffffff;
    --gold: #ebc73f;
    --gold-muted: #8c8350;
    --olive-rule: #8a8a8a;
    --tagline-grey: #666666;
  }
  * { margin: 0; padding: 0; box-sizing: border-box; }
  html, body { width: 1175px; height: 1200px; overflow: hidden; }
  body {
    position: relative;
    background: var(--stage);
    font-family: "Jost", sans-serif;
  }
  .card {
    position: absolute;
    left: 215px;
    width: 744px;
    height: 446px;
    box-shadow: 18px 22px 40px rgba(0,0,0,0.28);
    overflow: hidden;
  }
  .card--front { top: 111px; background: var(--charcoal); }
  .card--back { top: 617px; height: 447px; background: var(--white); }

  .brand-mark {
    position: absolute;
    left: 50%;
    border: 3px solid var(--gold-muted);
    transform: translateX(-50%);
  }
  .card--front .brand-mark { top: 132px; width: 72px; height: 72px; }
  .card--back .brand-mark { top: 55px; width: 62px; height: 62px; }

  .lockup {
    position: absolute;
    left: 50%;
    transform: translateX(-50%);
    text-align: center;
  }
  .lockup__name {
    font-family: "Montserrat", sans-serif;
    font-weight: 300;
    line-height: 1;
    white-space: nowrap;
  }
  .lockup__rule { height: 1.5px; margin-top: 10px; }
  .lockup__tag {
    display: flex;
    align-items: center;
    gap: 9px;
    margin-top: 6px;
    font-family: "Montserrat", sans-serif;
    font-weight: 700;
    white-space: nowrap;
  }
  .lockup__tag::before, .lockup__tag::after {
    content: "";
    flex: 1;
    height: 1.5px;
    background: currentColor;
  }

  .card--front .lockup { top: 254px; width: 330px; }
  .card--front .lockup__name { font-size: 55px; letter-spacing: 0.22em; margin-right: -0.22em; color: var(--white); }
  .card--front .lockup__rule { background: var(--white); }
  .card--front .lockup__tag { color: var(--white); font-size: 12.5px; letter-spacing: 0.42em; }

  .website {
    position: absolute;
    top: 387px;
    left: 0; right: 0;
    text-align: center;
    font-family: "Montserrat", sans-serif;
    font-weight: 500;
    font-size: 17px;
    color: var(--white);
  }

  .card--back .lockup { top: 150px; width: 262px; }
  .card--back .lockup__name { font-size: 44px; letter-spacing: 0.2em; margin-right: -0.2em; color: var(--ink); }
  .card--back .lockup__rule { background: var(--olive-rule); margin-top: 7px; }
  .card--back .lockup__tag { color: var(--tagline-grey); font-size: 10px; letter-spacing: 0.4em; margin-top: 4px; }

  .person {
    position: absolute;
    top: 232px;
    left: 0; right: 0;
    text-align: center;
  }
  .person__name {
    font-family: "Montserrat", sans-serif;
    font-weight: 500;
    font-size: 27px;
    color: var(--ink);
    line-height: 1;
  }
  .person__first { color: var(--gold); font-weight: 600; }
  .person__role {
    margin-top: 4px;
    font-size: 18px;
    font-weight: 500;
    color: var(--ink);
  }

  .band { position: absolute; left: 0; top: 0; width: 744px; height: 447px; }

  .contacts {
    position: absolute;
    top: 380px;
    left: 0; right: 0;
    height: 24px;
    color: var(--white);
    font-size: 19px;
    letter-spacing: 0.04em;
  }
  .contact {
    position: absolute;
    display: flex;
    align-items: center;
    gap: 8px;
    white-space: nowrap;
  }
  .contact--office { left: 66px; }
  .contact--cell { left: 300px; }
  .contact--mail { left: 485px; font-size: 18px; letter-spacing: 0; }
  .contact svg { fill: var(--white); flex: none; }
</style>
</head>
<body>

  <section class="card card--front" aria-label="Card front">
    <div class="brand-mark" aria-hidden="true"></div>
    <div class="lockup">
      <div class="lockup__name">BRISKEL</div>
      <div class="lockup__rule"></div>
      <div class="lockup__tag">LUXURY LANDSCAPES</div>
    </div>
    <div class="website">WWW.BRISKEL.CA</div>
  </section>

  <section class="card card--back" aria-label="Card back">
    <div class="brand-mark" aria-hidden="true"></div>
    <div class="lockup">
      <div class="lockup__name">BRISKEL</div>
      <div class="lockup__rule"></div>
      <div class="lockup__tag">LUXURY LANDSCAPES</div>
    </div>

    <div class="person">
      <div class="person__name"><span class="person__first">TOBIAS</span> FENNICK</div>
      <div class="person__role">Project manager</div>
    </div>

    <svg class="band" viewBox="0 0 744 447" aria-hidden="true">
      <defs>
        <linearGradient id="goldSweep" x1="0" y1="0" x2="1" y2="0">
          <stop offset="0" stop-color="#ebc73f"/>
          <stop offset="0.2" stop-color="#f5e29a"/>
          <stop offset="0.3" stop-color="#ffffff"/>
          <stop offset="0.5" stop-color="#ebc73f"/>
          <stop offset="0.7" stop-color="#ffffff"/>
          <stop offset="0.8" stop-color="#f5e29a"/>
          <stop offset="1" stop-color="#ebc73f"/>
        </linearGradient>
      </defs>
      <path d="M0 263 Q372 345 744 263 L744 447 L0 447 Z" fill="#333333"/>
      <path d="M0 278 Q372 338 744 278 L744 293 Q372 379 0 293 Z" fill="url(#goldSweep)"/>
    </svg>

    <div class="contacts">
      <div class="contact contact--office">
        <svg width="17" height="17" viewBox="0 0 24 24" aria-hidden="true"><path d="M6.6 10.8a15.1 15.1 0 0 0 6.6 6.6l2.2-2.2c.3-.3.7-.4 1-.2 1.1.4 2.3.6 3.6.6.6 0 1 .4 1 1V20c0 .6-.4 1-1 1A17 17 0 0 1 3 4c0-.6.4-1 1-1h3.5c.6 0 1 .4 1 1 0 1.3.2 2.5.6 3.6.1.3 0 .7-.2 1z"/></svg>
        <span>555-318-7094</span>
      </div>
      <div class="contact contact--cell">
        <svg width="13" height="18" viewBox="0 0 13 18" aria-hidden="true"><path d="M2 0h9a2 2 0 0 1 2 2v14a2 2 0 0 1-2 2H2a2 2 0 0 1-2-2V2a2 2 0 0 1 2-2zm0 2v11h9V2zm4.5 12.2a1 1 0 1 0 0 2 1 1 0 0 0 0-2z"/></svg>
        <span>555-642-1586</span>
      </div>
      <div class="contact contact--mail">
        <svg width="20" height="14" viewBox="0 0 20 14" aria-hidden="true"><path d="M0 0h20v14H0zm2 2v.3l8 5.6 8-5.6V2zm0 2.7V12h3.5l3-3.2zm16 0-6.5 4.1 3 3.2H18zM7.3 10 6.6 12h6.8l-.7-2L10 11.8z"/></svg>
        <span>Tobias@briskel-example.ca</span>
      </div>
    </div>
  </section>

</body>
</html>
```